Harbor Quillstead is a Smart Device integration/installation business

Hi, I am a tech enthusiast with a background in robotics, industrial automation and computers. I have currently launched a business to bring wireless voice controlled devices and smart devices into peoples homes at affordable prices, moving away from expensive smart wiring and programming installations. I fix bad wifi in houses and install new smart locks, multi-room audio, automated blinds etc. that can all be controlled through pimbly (zorvexa) or Tandrel Nest.

I need a modern and eye catching a5 flyer developed for post box drops that give people an understanding of what smart devices are - tandrel nest, zorvexa pimbly etc and how it can improve their lives. I have a couple of examples that I put together before realising that I need professional help. So please use these as a guide if they are helpful.

My website which also needs some work is: www.harborquillstead.net for some more ideas and info on the services I supply. I also have a facebook page with that business name for some recent posts.

If you need anymore info or idea on what I do let me know, cheers.

Target Market(s)

Pre-exisiting homes

Industry/Entity Type

Technology Equipment

Requirements
Must have
• My logo and business details mob and website

```html
<!DOCTYPE html>
<html lang="en">
<head>
<meta charset="utf-8">
<title>Harbor Quillstead – Smart Device Integration Flyer</title>
<link rel="stylesheet" href="https://fonts.googleapis.com/css2?family=Montserrat:wght@500;600&family=Open+Sans:wght@400&family=Roboto+Condensed:wght@400;700;800&display=swap">
<style>
  :root {
    --brand-blue: #1f6db3;
    --deep-blue: #17599a;
    --ink: #1c1c1c;
    --body-ink: #2a2a2a;
    --paper: #ffffff;
    --backdrop: #e4e4e4;
    --sky-top: #3d5f86;
    --sky-glow: #e88a4a;
    --city-dark: #2b3038;
  }
  * { box-sizing: border-box; margin: 0; padding: 0; }
  html, body { width: 1200px; height: 1200px; overflow: hidden; }
  body { background: var(--backdrop); position: relative; }

  .flyer {
    position: absolute; left: 210px; top: 50px;
    width: 780px; height: 1100px;
    background: var(--paper);
    overflow: hidden;
    box-shadow: 0 6px 24px rgba(0,0,0,.18);
  }

  .brand {
    position: absolute; left: 42px; top: 96px;
    display: flex; align-items: center; gap: 16px;
  }
  .brand-dot {
    width: 56px; height: 56px; border-radius: 50%;
    background: var(--brand-blue);
  }
  .brand-name {
    font-family: "Montserrat", sans-serif; font-weight: 600;
    font-size: 26px; color: var(--brand-blue); letter-spacing: .5px;
  }

  .title {
    position: absolute; right: 48px; top: 56px;
    font-family: "Roboto Condensed", sans-serif; line-height: .95;
  }
  .title-top { display: block; font-size: 40px; font-weight: 400; color: var(--ink); }
  .title-main { display: block; font-size: 48px; font-weight: 800; color: var(--brand-blue); }

  .hero { position: absolute; left: 0; top: 0; width: 780px; height: 1100px; }

  .copy { position: absolute; left: 48px; top: 615px; width: 690px; }
  .copy h2 {
    font-family: "Roboto Condensed", sans-serif; font-weight: 700;
    color: var(--brand-blue); font-size: 31px; line-height: 1.1;
  }
  .copy p {
    font-family: "Open Sans", sans-serif; font-size: 16px;
    line-height: 1.4; color: var(--body-ink); margin: 8px 0 20px;
  }

  .contact-band { position: absolute; left: 0; top: 0; width: 780px; height: 1100px; }
  .contact-heading {
    position: absolute; left: 44px; top: 1042px;
    font-family: "Roboto Condensed", sans-serif; font-weight: 700;
    font-size: 38px; line-height: 1; color: var(--paper);
  }
  .contact-item {
    position: absolute; display: flex; align-items: center; gap: 12px;
    font-family: "Roboto Condensed", sans-serif; font-size: 24px; line-height: 1; color: var(--paper);
  }
  .contact-phone { left: 300px; top: 1040px; }
  .contact-email { left: 480px; top: 988px; }
  .contact-item svg { width: 24px; height: 24px; }
</style>
</head>
<body>
  <main class="flyer">
    <svg class="hero" viewBox="0 0 780 1100">
      <defs>
        <linearGradient id="sky" x1="0" y1="0" x2="0" y2="1">
          <stop offset="0" stop-color="var(--sky-top)"/>
          <stop offset=".45" stop-color="var(--sky-glow)"/>
          <stop offset=".7" stop-color="var(--city-dark)"/>
          <stop offset="1" stop-color="#1e2229"/>
        </linearGradient>
      </defs>
      <path role="img" aria-label="Photo: hands holding a tablet showing an internet-of-things lightbulb graphic, in front of windows overlooking a city skyline at sunset with wifi symbols"
            d="M0 230 Q 390 215 780 150 L780 470 Q 400 520 0 600 Z" fill="url(#sky)"/>
      <path d="M0 226 Q 390 211 780 146" stroke="var(--brand-blue)" stroke-width="4" fill="none"/>
      <path d="M0 604 Q 400 524 780 474" stroke="var(--brand-blue)" stroke-width="4" fill="none"/>
    </svg>

    <div class="brand">
      <span class="brand-dot"></span>
      <span class="brand-name">Harbor Quillstead</span>
    </div>

    <h1 class="title">
      <span class="title-top">SMART DEVICE</span>
      <span class="title-main">INTEGRATION</span>
    </h1>

    <section class="copy">
      <h2>Your Smart Home Integration Professionals</h2>
      <p>We'll show you how these speaker powered voice activated Smart Assitants hold the key to your New Smart Home. Start building your new Smart Home with these devices starting</p>
      <h2>What exactactly is a Smart Assistant?”</h2>
      <p>Like Sorin, Kestra or Tandrel Helper on your smartphone, except for your home. An unpaid personal assitant doing all mundane tasks around your home. Combining these vitual assitants with speaker hardware allows you to turn your home into an automated, voice activated, app-controlled hub.</p>
    </section>

    <svg class="contact-band" viewBox="0 0 780 1100" aria-hidden="true">
      <path d="M0 1020 Q 420 990 780 930 L780 1100 L0 1100 Z" fill="var(--brand-blue)"/>
    </svg>
    <div class="contact-heading">Contact Us</div>
    <div class="contact-item contact-phone">
      <svg viewBox="0 0 24 24" aria-hidden="true"><path d="M6.6 10.8a15 15 0 0 0 6.6 6.6l2.2-2.2a1 1 0 0 1 1-.25 11.4 11.4 0 0 0 3.6.57 1 1 0 0 1 1 1V20a1 1 0 0 1-1 1A17 17 0 0 1 3 4a1 1 0 0 1 1-1h3.5a1 1 0 0 1 1 1c0 1.25.2 2.45.57 3.57a1 1 0 0 1-.25 1z" fill="#fff"/></svg>
      <span>0491 362 507</span>
    </div>
    <div class="contact-item contact-email">
      <svg viewBox="0 0 24 24" aria-hidden="true" fill="none" stroke="#fff" stroke-width="1.6"><circle cx="12" cy="12" r="9"/><path d="M3 12h18M12 3c3 3.2 3 14.8 0 18M12 3c-3 3.2-3 14.8 0 18"/></svg>
      <span>info@harborquillstead.net</span>
    </div>
  </main>
</body>
</html>
```